I need a letterhead for a newsletter that will go out quarterly to the dentists of the 18th district. It is called "The Crestline Digest" We are in Amarillo TX and have this landmark in the photo as our most prominent feature. If it could be used, that would be cool.
This is a professional organization newsletter so the letterhead should be somewhat professional.

Target Market(s)

Dentists

Industry/Entity Type

Dental

Font styles to use
Serif

Colors

Designer to choose only greyscale colors for use in the design.

Requirements
Must have
• I want the title of "The Crestline Digest" to be the on top with the phrase "Cobalt Ridge Dental Society" written underneath.
Nice to have
• the photo incorporated could be incorporated in black and white or color along the bottom of the letterhead or with the title inside the photo.
Should not have
• I don't want it to be cartoony. I want it to be stylish and elegant and professional.

```html
<!DOCTYPE html>
<html lang="en">
<head>
<meta charset="UTF-8">
<title>The Crestline Digest — Letterhead</title>
<link href="https://fonts.googleapis.com/css2?family=Marcellus+SC&display=swap" rel="stylesheet">
<style>
  :root {
    --backdrop: #dfe5f0;
    --paper: #ffffff;
    --band-blue: #0a7cc4;
    --title-blue: #0b78bd;
    --panel-light: #ffffff;
    --panel-dark: #cbcbcb;
    --photo-blue: #2a5aa8;
    --photo-orange: #d9683a;
  }
  * { margin: 0; padding: 0; box-sizing: border-box; }
  html, body {
    width: 1200px;
    height: 898px;
    overflow: hidden;
    background: var(--backdrop);
  }
  .letterhead-page {
    position: absolute;
    left: 268px;
    top: 19px;
    width: 664px;
    height: 860px;
    background: var(--paper);
    box-shadow: 0 6px 24px rgba(40, 55, 90, 0.18);
  }
  .masthead-band {
    position: absolute;
    left: 0;
    top: 0;
    width: 100%;
    height: 190px;
    background: var(--band-blue);
  }
  .masthead-card {
    position: absolute;
    left: 38px;
    top: 24px;
    right: 28px;
    bottom: 32px;
    display: flex;
    border: 2px solid #ffffff;
    border-radius: 22px;
    overflow: hidden;
  }
  .title-panel {
    width: 46%;
    background: linear-gradient(180deg, var(--panel-light) 0%, #ececec 45%, var(--panel-dark) 100%);
    display: flex;
    flex-direction: column;
    justify-content: center;
    padding: 34px 20px 0 24px;
  }
  .newsletter-title {
    font-family: "Marcellus SC", serif;
    color: var(--title-blue);
    font-size: 22px;
    font-weight: 400;
    line-height: 1.1;
    letter-spacing: 0.2px;
    white-space: nowrap;
  }
  .society-name {
    font-family: "Marcellus SC", serif;
    color: var(--title-blue);
    font-size: 11px;
    font-weight: 400;
    letter-spacing: 0.4px;
    margin-top: 6px;
    white-space: nowrap;
  }
  .landmark-photo {
    flex: 1;
    background: linear-gradient(135deg, var(--photo-blue) 0%, #6f7fa0 50%, var(--photo-orange) 100%);
  }
</style>
</head>
<body>
  <main class="letterhead-page">
    <header class="masthead-band">
      <div class="masthead-card">
        <div class="title-panel">
          <h1 class="newsletter-title">The Crestline Digest</h1>
          <p class="society-name">Cobalt Ridge Dental Society</p>
        </div>
        <div class="landmark-photo" role="img" aria-label="Photograph of a red sandstone canyon landmark under a blue sky"></div>
      </div>
    </header>
  </main>
</body>
</html>
```